Marlow Vale Stud website

We would like to create a horse stud/agistment farm website similar to this websites we have attached below:
www.thornbeck.com.au
www.quillstead.com.au
www.brackley.com
www.pimsey.com.au
The main colour scheme are purple and white to align with the stable's racing colours.
We have also attach the company logo and also images of the farm and create some ideas for the website.
Many thanks for looking into this project!

```html
<!DOCTYPE html>
<html lang="en">
<head>
<meta charset="utf-8">
<title>Marlow Vale Stud</title>
<link href="https://fonts.googleapis.com/css2?family=Montserrat:wght@400;600;700&family=Open+Sans:wght@400;600;700&display=swap" rel="stylesheet">
<style>
:root{
  --purple-deep:#2b0f33;
  --purple:#3d1747;
  --purple-accent:#5a2468;
  --ink:#222;
  --muted:#777;
  --panel:#f1f1f1;
  --white:#fff;
  --line:#ddd;
}
*{box-sizing:border-box;margin:0;padding:0}
html,body{width:1200px;height:3680px;overflow:hidden;background:var(--white)}
body{position:relative;font-family:"Open Sans",Arial,sans-serif;color:var(--ink)}
a{color:inherit;text-decoration:none}
.abs{position:absolute}

/* header */
.site-header{position:absolute;left:0;top:0;width:1200px;height:132px;background:var(--purple-deep);color:var(--white)}
.brand{position:absolute;left:90px;top:40px;display:flex;align-items:center;gap:16px;font-family:"Montserrat",sans-serif;font-weight:600;font-size:34px}
.brand-dot{width:46px;height:46px;border-radius:50%;border:3px solid var(--white)}
.topbar{position:absolute;right:92px;top:22px;display:flex;gap:40px;font-size:14px;align-items:center}
.topbar span{display:flex;align-items:center;gap:10px}
.main-nav{position:absolute;right:92px;top:72px;display:flex;gap:34px;font-size:17px}

/* hero */
.hero{position:absolute;left:0;top:132px;width:1200px;height:668px;background:linear-gradient(180deg,#1d5fb8 0%,#6fa0d6 40%,#b7cde2 60%,#5c8a3d 74%,#3f6f2a 100%)}
.hero-arrow{position:absolute;top:270px;color:var(--white);font-size:40px}
.hero-edge{position:absolute;left:0;bottom:0}

/* section titles */
.section-title{position:absolute;left:0;width:1200px;text-align:center;font-family:"Montserrat",sans-serif;font-weight:700;font-size:46px;letter-spacing:3px;color:var(--ink)}

/* services */
.service{position:absolute;top:990px;width:244px}
.service-photo{height:208px;border-radius:22px}
.service h3{margin-top:20px;font-family:"Montserrat",sans-serif;font-size:18px;font-weight:700}
.service p{margin-top:8px;font-size:13px;line-height:19px;color:var(--muted)}
.more{display:block;margin-top:8px;font-size:13px;font-weight:700;color:var(--purple)}
.slider-dots{position:absolute;top:1378px;left:564px;display:flex;gap:10px}
.slider-dots i{width:22px;height:22px;border-radius:50%;border:2px solid #555;display:block}
.slider-dots i.on{background:#444}

/* welcome */
.welcome{position:absolute;left:0;top:1512px;width:1200px;height:488px;background:var(--panel)}
.welcome-photo{position:absolute;left:0;top:0;width:580px;height:488px;background:linear-gradient(180deg,#3a2a2a 0%,#6a4d3b 45%,#c9a77a 70%,#6b8c47 100%)}
.welcome-curve{position:absolute;left:0;top:0}
.welcome-text{position:absolute;left:766px;top:98px;width:380px}
.welcome-text h2{font-family:"Montserrat",sans-serif;font-weight:700;font-size:44px;line-height:50px;letter-spacing:2px}
.welcome-text p{margin-top:24px;font-size:14px;line-height:22px;color:#555}
.welcome-text b{color:var(--purple)}

/* news */
.news-card{position:absolute;top:2160px;width:320px;height:420px;border:1px solid var(--line);background:var(--white)}
.news-photo{position:absolute;left:10px;top:10px;width:298px;height:200px}
.news-date{position:absolute;left:24px;top:168px;width:60px;height:70px;background:var(--purple);color:var(--white);text-align:center;font-family:"Montserrat",sans-serif;font-weight:700;padding-top:8px;font-size:24px;line-height:28px}
.news-date small{display:block;font-size:15px}
.news-card h3{position:absolute;left:18px;top:254px;width:280px;font-size:17px;line-height:23px;font-weight:700}
.news-card p{position:absolute;left:18px;top:308px;width:284px;font-size:13px;line-height:19px;color:var(--muted)}
.news-card .more{position:absolute;left:18px;top:378px;margin:0}
.news-arrow{position:absolute;top:2340px;font-size:34px;color:#333}

/* gallery */
.gallery-tile{position:absolute}

/* footer */
.site-footer{position:absolute;left:0;top:3220px;width:1200px;height:460px;background:var(--purple-deep);color:var(--white)}
.footer-col{position:absolute;top:170px;font-size:13px;line-height:21px;color:#ddd}
.footer-col h4{font-family:"Montserrat",sans-serif;font-weight:600;font-size:22px;color:var(--white);margin-bottom:18px}
.signup{display:flex;margin-top:14px}
.signup span{width:220px;height:40px;background:var(--white);color:#999;padding:9px 12px}
.signup b{width:44px;height:40px;background:#111;color:var(--white);text-align:center;line-height:40px}
.socials{display:flex;gap:10px;margin-top:16px}
.socials i{width:30px;height:30px;border-radius:50%;display:block}
.copyright{position:absolute;left:0;bottom:0;width:1200px;height:50px;border-top:1px solid #4d2a57;text-align:center;line-height:50px;font-size:12px;color:#ccc}
</style>
</head>
<body>

<header class="site-header">
  <div class="brand"><span class="brand-dot"></span>Marlow Vale Stud</div>
  <div class="topbar">
    <span><svg width="16" height="16" viewBox="0 0 24 24"><path fill="#fff" d="M6.6 10.8a15 15 0 0 0 6.6 6.6l2.2-2.2c.3-.3.7-.4 1-.2 1.1.4 2.3.6 3.6.6.6 0 1 .4 1 1V20c0 .6-.4 1-1 1A17 17 0 0 1 3 4c0-.6.4-1 1-1h3.5c.6 0 1 .4 1 1 0 1.3.2 2.5.6 3.6.1.3 0 .7-.2 1z"/></svg>+61 400 118 275</span>
    <span><svg width="18" height="14" viewBox="0 0 18 14"><rect x="1" y="1" width="16" height="12" fill="none" stroke="#fff" stroke-width="1.6"/><path d="M1 1l8 7 8-7" fill="none" stroke="#fff" stroke-width="1.6"/></svg>hello@marlowvalestud.com</span>
  </div>
  <nav class="main-nav"><a>Home</a><a>About Us</a><a>Stallions</a><a>Sales</a><a>Gallery</a><a>News</a><a>Contact Us</a></nav>
</header>

<section class="hero" role="img" aria-label="Five young horses standing in a green paddock under a blue sky">
  <span class="hero-arrow" style="left:30px">&#8249;</span>
  <span class="hero-arrow" style="right:30px">&#8250;</span>
  <svg class="hero-edge" width="1200" height="70" viewBox="0 0 1200 70" preserveAspectRatio="none"><path fill="#fff" d="M0 40 L60 30 L120 44 L200 26 L260 42 L340 30 L420 46 L500 28 L580 40 L660 24 L740 42 L820 30 L900 46 L980 28 L1060 40 L1140 26 L1200 36 L1200 70 L0 70Z"/></svg>
</section>

<h2 class="section-title" style="top:900px">OUR SERVICES</h2>

<article class="service" style="left:88px">
  <div class="service-photo" role="img" aria-label="Pale stallion standing in a paddock" style="background:linear-gradient(180deg,#9cc0e0,#c7b79a 55%,#6f9a4a)"></div>
  <h3>SILVER HOLLOW (USA)</h3>
  <p>Silver Hollow (USA) Double-stake thoroughbred stallion.</p>
  <a class="more">Learn More &#187;</a>
</article>
<article class="service" style="left:348px">
  <div class="service-photo" role="img" aria-label="Young horse being broken in a round yard" style="background:linear-gradient(180deg,#4e6b3a,#8a6a48 55%,#5c7c3a)"></div>
  <h3>BREAKING</h3>
  <p>Breaking: the education of yearling horses.</p>
  <a class="more">Learn More &#187;</a>
</article>
<article class="service" style="left:608px">
  <div class="service-photo" role="img" aria-label="Chestnut horse in an outdoor arena" style="background:linear-gradient(180deg,#6f8d4f,#a9703f 55%,#7e9a4d)"></div>
  <h3>FACILITY HIRE</h3>
  <p>Indoor Arena, Outdoor Arena and various sized yards.</p>
  <a class="more">Learn More &#187;</a>
</article>
<article class="service" style="left:868px">
  <div class="service-photo" role="img" aria-label="Horses grazing in an agistment paddock" style="background:linear-gradient(180deg,#8fa6b8,#76855a 55%,#55703a)"></div>
  <h3>AGISTMENT</h3>
  <p>All agistment services are available and can tailor to individual needs.</p>
  <a class="more">Learn More &#187;</a>
</article>
<div class="slider-dots"><i class="on"></i><i></i></div>

<section class="welcome">
  <div class="welcome-photo" role="img" aria-label="Jockey in purple silks riding a grey racehorse past a flower bed"></div>
  <svg class="welcome-curve" width="620" height="488" viewBox="0 0 620 488"><path d="M540 0 Q640 244 540 488 L620 488 L620 0Z" fill="#f1f1f1"/><path d="M540 0 Q640 244 540 488" fill="none" stroke="#3d1747" stroke-width="10"/></svg>
  <div class="welcome-text">
    <h2>WELCOME TO<br>MARLOW VALE STUD</h2>
    <p>Lorem ipsum dolor sit amet, consectetur adipiscing elit, sed do eiusmod tempor incididunt ut labore et dolore magna aliqua. Ut enim ad minim veniam, quis nostrud exercitation ullamco laboris nisi ut aliquip ex ea commodo consequat. Duis aute irure dolor in reprehenderit in voluptate velit esse cillum dolore eu fugiat nulla pariatur. <b>Continue Reading</b></p>
  </div>
</section>

<h2 class="section-title" style="top:2086px">NEWS</h2>
<span class="news-arrow" style="left:60px">&#8249;</span>
<span class="news-arrow" style="right:60px">&#8250;</span>

<article class="news-card" style="left:100px">
  <div class="news-photo" role="img" aria-label="Racehorse and jockey at the track" style="background:linear-gradient(180deg,#8a6b7a,#5a7a4a 60%,#c49a5a)"></div>
  <div class="news-date">25<small>FEB</small></div>
  <h3>Lorem ipsum dolor sit amet, consectetur adipiscing</h3>
  <p>Lorem ipsum dolor sit amet, consectetur adipiscing elit, sed do eiusmod tempor incididunt ut labore et dolore.</p>
  <a class="more">READ MORE</a>
</article>
<article class="news-card" style="left:440px">
  <div class="news-photo" role="img" aria-label="Stable building with red roof" style="background:linear-gradient(180deg,#9fb8cf,#7a2a2a 45%,#5a6a3a)"></div>
  <div class="news-date">25<small>FEB</small></div>
  <h3>Lorem ipsum dolor sit amet, consectetur adipiscing</h3>
  <p>Lorem ipsum dolor sit amet, consectetur adipiscing elit, sed do eiusmod tempor incididunt ut labore et dolore.</p>
  <a class="more">READ MORE</a>
</article>
<article class="news-card" style="left:780px">
  <div class="news-photo" role="img" aria-label="Aerial view of the farm and arena" style="background:linear-gradient(180deg,#6f8f4a,#b8a58a 50%,#4f7a35)"></div>
  <div class="news-date">25<small>FEB</small></div>
  <h3>Lorem ipsum dolor sit amet, consectetur adipiscing</h3>
  <p>Lorem ipsum dolor sit amet, consectetur adipiscing elit, sed do eiusmod tempor incididunt ut labore et dolore.</p>
  <a class="more">READ MORE</a>
</article>

<h2 class="section-title" style="top:2676px">GALLERY</h2>
<div class="gallery-tile" role="img" aria-label="Aerial view of farm buildings among green paddocks" style="left:100px;top:2760px;width:480px;height:222px;background:linear-gradient(180deg,#7fa3c6,#8f9a6a 40%,#5a7a3a)"></div>
<div class="gallery-tile" role="img" aria-label="Tree-lined driveway" style="left:590px;top:2760px;width:250px;height:222px;background:linear-gradient(180deg,#3f5a2a,#b9a27a 70%,#6a7a3a)"></div>
<div class="gallery-tile" role="img" aria-label="Horses in a green field under blue sky" style="left:850px;top:2760px;width:250px;height:222px;background:linear-gradient(180deg,#4a82c8,#a8c2dc 40%,#4f7a2f)"></div>
<div class="gallery-tile" role="img" aria-label="Chestnut horse grazing" style="left:100px;top:2992px;width:250px;height:228px;background:linear-gradient(180deg,#9fb8cf,#9a6a3a 55%,#5a8a3a)"></div>
<div class="gallery-tile" role="img" aria-label="Stable yard with fences" style="left:360px;top:2992px;width:250px;height:228px;background:linear-gradient(180deg,#8aa4bd,#6a6a5a 50%,#5a7a3a)"></div>
<div class="gallery-tile" role="img" aria-label="Wide green paddock with trees" style="left:620px;top:2992px;width:480px;height:228px;background:linear-gradient(180deg,#7a9ab8,#6a8a4a 50%,#3f6a2a)"></div>

<footer class="site-footer">
  <svg class="abs" style="left:0;top:0" width="1200" height="80" viewBox="0 0 1200 80" preserveAspectRatio="none"><path fill="#fff" d="M0 0 L1200 0 L1200 30 L1130 44 L1060 26 L980 46 L900 30 L820 48 L740 28 L660 44 L580 26 L500 46 L420 30 L340 48 L260 28 L180 44 L100 26 L40 40 L0 30Z"/></svg>
  <div class="footer-col" style="left:88px">
    <h4>Contact Us</h4>
    COMPANY<br>12 Orchard Lane, Northvale QLD 4000<br><br>EMAIL ADDRESS<br>hello@marlowvalestud.com<br><br>CALL US<br>+61 400 118 275
  </div>
  <div class="footer-col" style="left:420px">
    <h4>Links</h4>
    Home<br>About Us<br>Stallions<br>Sales<br>Gallery<br>News
  </div>
  <div class="footer-col" style="left:640px">
    <h4>Legal</h4>
    Support<br>Faq<br>Sitemap<br>Contact Us
  </div>
  <div class="footer-col" style="left:872px">
    <h4>Newsletter</h4>
    For exclusive news and updates sign up<br>for our newsletter.
    <div class="signup"><span>Email address</span><b>&#10148;</b></div>
    <div class="socials"><i style="background:#c0392b"></i><i style="background:#c0392b"></i><i style="background:#2d5fa8"></i><i style="background:#3fa3e0"></i><i style="background:#2a6fb0"></i></div>
  </div>
  <div class="copyright">&#169; 2016 Copyright THE COMPANY NAME All Rights Reserved | Privacy Policy, Terms of Service</div>
</footer>

</body>
</html>
```